Corvana - Waste to Fuel Power Needs A Website

Make website explaining the concept and the team behind the company
Updates

I will be providing A logo and Information about the company upon signed NDA.

Coding

Coded - Design and coding required

Number of Pages Required

5+ page

```html
<!DOCTYPE html>
<html lang="en">
<head>
<meta charset="utf-8">
<title>Corvana - Waste to Fuel Power</title>
<link href="https://fonts.googleapis.com/css2?family=Poppins:wght@300;400;500;600;700&display=swap" rel="stylesheet">
<style>
:root{
  --blue:#1a6fc0;
  --green:#5dbb3f;
  --ink:#1f2328;
  --muted:#5b6168;
  --grey-bg:#eeeeee;
  --dark:#1d1f23;
  --white:#ffffff;
  --star:#f5b301;
}
*{box-sizing:border-box;margin:0;padding:0}
html,body{width:1200px;height:3344px;overflow:hidden}
body{font-family:"Poppins",sans-serif;color:var(--ink);background:var(--white);position:relative}
section,header,footer{position:absolute;left:0;width:1200px}

/* hero */
.hero{top:0;height:590px;background:linear-gradient(135deg,#2a1d10 0%,#6b4318 38%,#b47a2c 55%,#3a2612 80%,#1b140c 100%)}
.hero-shade{position:absolute;inset:0;background:rgba(10,10,10,.45)}
.nav{position:absolute;top:0;left:0;width:1200px;height:80px;display:flex;align-items:center;justify-content:space-between;padding:0 70px;z-index:2}
.brand{display:flex;align-items:center;gap:10px;color:var(--white);font-weight:600;font-size:26px}
.brand-dot{width:16px;height:16px;border-radius:50%;background:var(--green)}
.nav-links{display:flex;gap:34px;list-style:none}
.nav-links a{color:var(--white);text-decoration:none;font-size:15px;font-weight:500;padding-bottom:6px}
.nav-links .active{border-bottom:2px solid var(--white);font-weight:600}
.hero-body{position:absolute;top:160px;left:0;width:1200px;text-align:center;color:var(--white);z-index:2}
.hero-body h1{font-size:44px;font-weight:700;line-height:1.2}
.hero-body h2{font-size:44px;font-weight:300;line-height:1.2}
.hero-body p{width:640px;margin:22px auto 0;font-size:15px;line-height:1.6;color:#e8e8e8}
.btn{display:inline-block;margin-top:28px;background:var(--green);color:var(--white);font-size:15px;font-weight:500;padding:12px 30px;border-radius:6px;text-decoration:none}

/* problem */
.problem{top:590px;height:550px;padding:80px 0 0 110px}
.problem-text{width:560px}
.h-split .lead{display:block;color:var(--blue);font-weight:700;font-size:38px;line-height:1.15}
.h-split .rest{display:block;color:var(--ink);font-weight:300;font-size:38px;line-height:1.2}
.problem-text p{margin-top:18px;font-size:15px;line-height:1.65;color:var(--muted)}
.benefits-title{margin-top:20px;font-weight:600;color:var(--blue);font-size:16px}
.benefits{list-style:none;margin-top:10px}
.benefits li{font-size:15px;color:var(--muted);line-height:2;display:flex;align-items:center;gap:12px}
.benefits svg{width:14px;height:14px}
.problem-art{position:absolute;top:60px;right:110px;width:400px;height:400px;border-radius:16px;background:linear-gradient(135deg,#e6e9ee 0%,#d9dde3 100%)}

/* how */
.how{top:1140px;height:630px;background:var(--grey-bg)}
.section-title{text-align:center;font-size:38px;font-weight:600;color:var(--ink);padding-top:70px}
.section-title b{color:var(--blue);font-weight:700}
.how-ring{position:absolute;top:200px;left:420px;width:360px;height:360px;border-radius:50%;border:2px dashed #b9b9b9}
.how-art{position:absolute;top:230px;left:450px;width:300px;height:300px;border-radius:50%;background:radial-gradient(circle at 50% 45%,#343a42 0%,#1e2227 100%)}
.step{position:absolute;width:330px;display:flex;gap:16px;align-items:flex-start}
.step .icon{flex:none;width:58px;height:58px;border-radius:50%;background:var(--green);display:flex;align-items:center;justify-content:center}
.step h3{font-size:18px;font-weight:600;margin-bottom:4px}
.step p{font-size:14px;line-height:1.5;color:var(--muted)}
.step.left{flex-direction:row-reverse;text-align:right;left:80px}
.step.right{left:790px}
.step.top{top:250px}
.step.bottom{top:430px}

/* team */
.team{top:1770px;height:630px;padding:70px 110px 0}
.team .h-split .lead,.team .h-split .rest{font-size:36px}
.team-intro{margin-top:12px;width:800px;font-size:15px;line-height:1.6;color:var(--muted)}
.arrows{position:absolute;top:190px;right:110px;display:flex;gap:12px}
.arrow{width:46px;height:46px;border-radius:50%;display:flex;align-items:center;justify-content:center;border:2px solid var(--green)}
.arrow.solid{background:var(--green)}
.cards{display:flex;gap:24px;margin-top:40px}
.member{width:227px;height:330px;border:1px solid #d6d6d6;border-radius:12px;padding:12px;text-align:center}
.member .photo{height:220px;border-radius:8px}
.member h4{margin-top:16px;font-size:17px;font-weight:500}
.member span{font-size:13px;color:var(--muted)}
.p1{background:linear-gradient(#d9d9d9,#3b4048)}
.p2{background:linear-gradient(#1c2430,#3a4a62)}
.p3{background:linear-gradient(#f4b03a,#c37b22)}
.p4{background:linear-gradient(#c8d0d8,#6e7680)}

/* testimonials */
.testimonials{top:2400px;height:630px;background:var(--grey-bg)}
.quotes{display:flex;gap:30px;justify-content:center;margin-top:50px}
.quote{width:316px;height:310px;background:var(--white);border-radius:12px;padding:30px 26px;position:relative;box-shadow:0 2px 8px rgba(0,0,0,.06)}
.quote .mark{position:absolute;top:-26px;right:40px;font-size:76px;font-weight:700;color:var(--green);line-height:1}
.quote p{margin-top:22px;font-size:14px;line-height:1.6;color:var(--muted)}
.quote .who{position:absolute;left:26px;bottom:28px;font-size:14px;font-weight:600}
.stars{display:block;color:var(--star);font-size:15px;letter-spacing:2px}
.quote .badge{position:absolute;right:26px;bottom:30px;width:34px;height:34px;border-radius:50%;background:#d9d9d9}
.dots{display:flex;gap:10px;justify-content:center;margin-top:34px}
.dots i{width:12px;height:12px;border-radius:50%;background:#c6c6c6}
.dots i.on{background:var(--blue)}

/* footer */
.footer{top:3030px;height:314px;background:var(--dark);color:var(--white);text-align:center;padding-top:60px}
.footer .brand{justify-content:center;font-size:34px}
.footer-links{display:flex;gap:34px;justify-content:center;list-style:none;margin-top:48px}
.footer-links a{color:var(--white);text-decoration:none;font-size:15px}
.footer hr{width:580px;margin:22px auto 0;border:0;border-top:1px solid #50545b}
.copy{margin-top:18px;font-size:13px;color:#c8c8c8}
</style>
</head>
<body>

<header class="hero" role="img" aria-label="Close-up of golden diesel fuel pouring from an industrial nozzle">
  <div class="hero-shade"></div>
  <nav class="nav">
    <div class="brand"><span class="brand-dot"></span>Corvana</div>
    <ul class="nav-links">
      <li><a class="active" href="#">Home</a></li>
      <li><a href="#">Technology</a></li>
      <li><a href="#">Environmental Impact</a></li>
      <li><a href="#">Team</a></li>
      <li><a href="#">Contact</a></li>
    </ul>
  </nav>
  <div class="hero-body">
    <h1>Turning Plastic Waste into</h1>
    <h2>Clean Diesel Energy</h2>
    <p>Corvana converts non-recyclable plastic into high-quality diesel fuel – reducing landfill waste while powering commercial industries.</p>
    <a class="btn" href="#">Learn How It Works</a>
  </div>
</header>

<section class="problem">
  <div class="problem-text">
    <h2 class="h-split"><span class="lead">The World Has a</span><span class="rest">Plastic Waste Problem</span></h2>
    <p>Every year, millions of tons of plastic end up in landfills and oceans. Much of this plastic cannot be recycled using traditional methods. Corvana provides a solution by converting waste plastic into usable diesel fuel through advanced thermal conversion technology.</p>
    <div class="benefits-title">Benefits:</div>
    <ul class="benefits">
      <li><svg viewBox="0 0 14 14"><path d="M2 7h9M7 3l4 4-4 4" fill="none" stroke="#5b6168" stroke-width="1.6"/></svg>Reduces landfill waste</li>
      <li><svg viewBox="0 0 14 14"><path d="M2 7h9M7 3l4 4-4 4" fill="none" stroke="#5b6168" stroke-width="1.6"/></svg>Converts non-recyclable plastics</li>
      <li><svg viewBox="0 0 14 14"><path d="M2 7h9M7 3l4 4-4 4" fill="none" stroke="#5b6168" stroke-width="1.6"/></svg>Produces commercial fuel</li>
      <li><svg viewBox="0 0 14 14"><path d="M2 7h9M7 3l4 4-4 4" fill="none" stroke="#5b6168" stroke-width="1.6"/></svg>Supports circular energy systems</li>
    </ul>
  </div>
  <div class="problem-art" role="img" aria-label="Illustration of recycled plastic pieces and a drop of fuel"></div>
</section>

<section class="how">
  <h2 class="section-title"><b>How</b> Corvana Works</h2>
  <div class="how-ring"></div>
  <div class="how-art" role="img" aria-label="Photo of a fuel nozzle releasing diesel drops"></div>

  <div class="step left top">
    <div class="icon"><svg width="28" height="28" viewBox="0 0 28 28"><path d="M14 3c4 6 7 9 7 14a7 7 0 0 1-14 0c0-5 3-8 7-14z" fill="#fff"/></svg></div>
    <div><h3>Thermal Conversion</h3><p>Plastic is heated without oxygen, breaking it into oil vapour for recovery.</p></div>
  </div>
  <div class="step right top">
    <div class="icon"><svg width="28" height="28" viewBox="0 0 28 28"><rect x="8" y="4" width="12" height="20" rx="2" fill="#fff"/></svg></div>
    <div><h3>Fuel Refinement</h3><p>Recovered oil is refined and filtered into clean, usable diesel fuel.</p></div>
  </div>
  <div class="step left bottom">
    <div class="icon"><svg width="28" height="28" viewBox="0 0 28 28"><path d="M6 9h16l-2 15H8z M10 5h8v3h-8z" fill="#fff"/></svg></div>
    <div><h3>Plastic Collection</h3><p>Waste plastic is gathered from partners, sorted and prepared for processing.</p></div>
  </div>
  <div class="step right bottom">
    <div class="icon"><svg width="28" height="28" viewBox="0 0 28 28"><path d="M16 3L6 16h7l-2 9 10-13h-7z" fill="#fff"/></svg></div>
    <div><h3>Energy Distribution</h3><p>Finished fuel is delivered to commercial clients and industrial sites.</p></div>
  </div>
</section>

<section class="team">
  <h2 class="h-split"><span class="lead">Our</span><span class="rest">Team Members</span></h2>
  <p class="team-intro">Meet the engineers and founders behind Corvana, working together to turn discarded plastic into reliable energy for industry and communities.</p>
  <div class="arrows">
    <div class="arrow solid"><svg width="16" height="16" viewBox="0 0 16 16"><path d="M10 3L5 8l5 5" fill="none" stroke="#fff" stroke-width="2"/></svg></div>
    <div class="arrow"><svg width="16" height="16" viewBox="0 0 16 16"><path d="M6 3l5 5-5 5" fill="none" stroke="#5dbb3f" stroke-width="2"/></svg></div>
  </div>
  <div class="cards">
    <div class="member"><div class="photo p1" role="img" aria-label="Portrait of co-founder Daniel Hart"></div><h4>Daniel Hart</h4><span>Co-Founder</span></div>
    <div class="member"><div class="photo p2" role="img" aria-label="Portrait of co-founder Owen Ridley"></div><h4>Owen Ridley</h4><span>Co-Founder</span></div>
    <div class="member"><div class="photo p3" role="img" aria-label="Portrait of co-founder Clara Voss"></div><h4>Clara Voss</h4><span>Co-Founder</span></div>
    <div class="member"><div class="photo p4" role="img" aria-label="Portrait of co-founder Ethan Marlow"></div><h4>Ethan Marlow</h4><span>Co-Founder</span></div>
  </div>
</section>

<section class="testimonials">
  <h2 class="section-title"><b>Our</b> Testimonials</h2>
  <div class="quotes">
    <div class="quote"><span class="mark">&rdquo;</span><p>Working with Corvana changed how we handle plastic waste. Their team was clear, fast and professional, and the fuel quality met every standard we needed for our fleet.</p><div class="who">DANIEL HART<span class="stars">★★★★★</span></div><span class="badge"></span></div>
    <div class="quote"><span class="mark">&rdquo;</span><p>Working with Corvana changed how we handle plastic waste. Their team was clear, fast and professional, and the fuel quality met every standard we needed for our fleet.</p><div class="who">DANIEL HART<span class="stars">★★★★★</span></div><span class="badge"></span></div>
    <div class="quote"><span class="mark">&rdquo;</span><p>Working with Corvana changed how we handle plastic waste. Their team was clear, fast and professional, and the fuel quality met every standard we needed for our fleet.</p><div class="who">DANIEL HART<span class="stars">★★★★★</span></div><span class="badge"></span></div>
  </div>
  <div class="dots"><i class="on"></i><i></i><i></i><i></i></div>
</section>

<footer class="footer">
  <div class="brand"><span class="brand-dot"></span>Corvana</div>
  <ul class="footer-links">
    <li><a href="#">Home</a></li>
    <li><a href="#">Technology</a></li>
    <li><a href="#">Environmental Impact</a></li>
    <li><a href="#">Team</a></li>
    <li><a href="#">Contact</a></li>
  </ul>
  <hr>
  <p class="copy">Copyright © 2025 Corvana. All rights reserved.</p>
</footer>

</body>
</html>
```